KDWB Business Card

Looking for a business card design to incorporate our branding. We want to only use the colors listing in the Branding Package (attached).
Updates

Target Market(s)

People who need their phone or device fixed.

Industry/Entity Type

Electronics

Contact Information for Business Card

Please use:

Brightwick Gadget Clinic LLC
4810 E Harlow Ridge Rd
Suite 417
San Antonio, TX 78163

Marcus Delgrove, Store Manager

(210) 555-0147

Requirements
Must have
• Must include the colors that are contained within the Branding Package PDF file.

```html
<!DOCTYPE html>
<html lang="en">
<head>
<meta charset="utf-8">
<title>Brightwick Gadget Clinic – Business Card</title>
<link rel="stylesheet" href="https://fonts.googleapis.com/css2?family=Heebo:wght@300;400;500&display=swap">
<style>
  :root {
    --stage: #d6d6d4;
    --silver-light: #f2f2f0;
    --silver-mid: #c9c7c2;
    --silver-dark: #a9a7a2;
    --ink: #050505;
    --ink-soft: #222222;
    --brand-red: #c8281f;
    --name-white: #e6e6e6;
    --phone-grey: #8d8179;
    --divider: #4a4a4a;
  }
  html, body {
    margin: 0;
    width: 1200px;
    height: 1200px;
    overflow: hidden;
    background: var(--stage);
  }
  .stage {
    width: 1200px;
    height: 1200px;
    display: flex;
    align-items: center;
    justify-content: center;
  }
  .business-card {
    width: 1000px;
    height: 599px;
    display: block;
    box-shadow: 0 10px 30px rgba(0,0,0,0.18);
    font-family: "Heebo", "Helvetica Neue", Arial, sans-serif;
  }
  .brand-name { fill: var(--brand-red); font-weight: 500; font-size: 46px; letter-spacing: -0.5px; }
  .person-name { fill: var(--name-white); font-weight: 300; font-size: 46px; letter-spacing: -0.5px; }
  .person-title { fill: var(--brand-red); font-weight: 300; font-size: 27px; }
  .phone-number { fill: var(--phone-grey); font-weight: 300; font-size: 28px; letter-spacing: 0.5px; }
</style>
</head>
<body>
<main class="stage">
  <svg class="business-card" viewBox="0 0 1070 641" xmlns="http://www.w3.org/2000/svg" aria-label="Business card for Brightwick Gadget Clinic">
    <defs>
      <linearGradient id="silverFace" x1="0" y1="0" x2="1" y2="0.4">
        <stop offset="0" stop-color="var(--silver-light)"/>
        <stop offset="0.35" stop-color="var(--silver-mid)"/>
        <stop offset="0.55" stop-color="var(--silver-light)"/>
        <stop offset="0.8" stop-color="var(--silver-dark)"/>
        <stop offset="1" stop-color="var(--silver-mid)"/>
      </linearGradient>
      <linearGradient id="inkPanel" x1="0" y1="0" x2="1" y2="0">
        <stop offset="0" stop-color="var(--ink-soft)"/>
        <stop offset="0.5" stop-color="var(--ink-soft)"/>
        <stop offset="0.6" stop-color="var(--ink)"/>
        <stop offset="1" stop-color="var(--ink)"/>
      </linearGradient>
    </defs>

    <!-- silver face -->
    <rect class="card-face" width="1070" height="641" fill="url(#silverFace)"/>

    <!-- brand lockup -->
    <g class="brand-lockup">
      <rect class="brand-square" x="139" y="110" width="108" height="108" rx="14" fill="var(--brand-red)"/>
      <text class="brand-name" x="272" y="180">Brightwick Gadget Clinic</text>
    </g>

    <!-- swoosh accents -->
    <path class="swoosh-upper" d="M82,302 C300,400 560,390 760,300 C880,250 960,215 1040,212 C960,222 880,255 770,310 C560,405 300,410 82,302 Z" fill="var(--ink)"/>
    <path class="swoosh-lower" d="M0,300 C160,380 360,420 540,385 C380,435 170,410 0,318 Z" fill="#2a2a2a"/>

    <!-- dark lower panel -->
    <path class="ink-panel" d="M0,318 C170,400 360,440 560,395 C760,345 900,240 1070,230 L1070,641 L0,641 Z" fill="url(#inkPanel)"/>

    <!-- contact block -->
    <g class="contact-block">
      <text class="person-name" x="118" y="524">Marcus Delgrove</text>
      <text class="person-title" x="118" y="562">Store Manager</text>
      <line class="divider" x1="532" y1="455" x2="532" y2="606" stroke="var(--divider)" stroke-width="2"/>
      <g class="phone-icon">
        <rect x="602" y="516" width="28" height="28" fill="var(--brand-red)"/>
        <path d="M610,522 l4,0 l2,5 l-3,2 c1,3 3,5 6,6 l2,-3 l5,2 l0,4 c-9,1 -17,-7 -16,-16 z" fill="#1a1a1a"/>
      </g>
      <text class="phone-number" x="642" y="540">(210) 555-0147</text>
    </g>
  </svg>
</main>
</body>
</html>
```